Looking for a modern, Professional business card design

We have a simple business card, but are looking for a more modern, professional look. A sample of the basic card is attached as well as the logo. We would also like to add that we offer:
Struggling with your finances?
- Learn to become debt free
- Discover the power of cash
- Control your money instead of it controlling you
Let us help you achieve a new level of financial freedom!
Also, we would like to have a "SPECIAL OFFER!: FREE 30 minute consultation"
Financial Planning

```html
<!DOCTYPE html>
<html lang="en">
<head>
<meta charset="utf-8">
<title>Clearpath Money Coaching – Business Card</title>
<link href="https://fonts.googleapis.com/css2?family=Roboto:wght@400;500;700&family=Open+Sans:ital,wght@0,400;0,600;0,700;1,700&family=Open+Sans+Condensed:wght@700&display=swap" rel="stylesheet">
<style>
  :root {
    --lime: #98c93c;
    --lime-dark: #4f7a1d;
    --forest: #3b8a3e;
    --text-green: #3a9a3a;
    --ink: #1e1e1e;
    --white: #ffffff;
    --backdrop: #e9ebe6;
  }
  * { margin: 0; padding: 0; box-sizing: border-box; }
  html, body { width: 1200px; height: 900px; overflow: hidden; }
  body { background: var(--backdrop); position: relative; font-family: "Open Sans", Arial, sans-serif; }

  .card { position: absolute; background: var(--white); overflow: hidden; box-shadow: 0 4px 14px rgba(0,0,0,.18); }

  /* Front */
  .card-front { left: 238px; top: 62px; width: 555px; height: 343px; font-family: "Roboto", Arial, sans-serif; }
  .front-top-band { position: absolute; left: 0; top: 0; width: 100%; height: 76px; background: var(--lime); border-bottom: 3px solid var(--lime-dark); }
  .front-mark { position: absolute; left: 62px; top: 108px; width: 80px; height: 80px; border-radius: 50%; background: var(--lime); }
  .holder-name { position: absolute; left: 142px; top: 120px; font-size: 32px; font-weight: 500; color: var(--ink); letter-spacing: .3px; }
  .holder-role { position: absolute; left: 142px; top: 162px; font-size: 15px; color: var(--ink); letter-spacing: .3px; }
  .front-contact-band { position: absolute; left: 0; top: 214px; width: 100%; height: 129px; background: var(--forest); }
  .contact-list { position: absolute; left: 142px; top: 30px; width: 297px; list-style: none; }
  .contact-list li { display: flex; align-items: center; gap: 8px; height: 23px; border-bottom: 1px solid rgba(255,255,255,.7); color: var(--white); font-size: 15.5px; }
  .contact-list svg { width: 12px; height: 12px; fill: var(--white); flex: none; }

  /* Back */
  .card-back { left: 459px; top: 518px; width: 560px; height: 343px; }
  .brand { position: absolute; left: 0; right: 0; top: 50px; display: flex; justify-content: center; align-items: center; gap: 10px; }
  .brand-dot { width: 26px; height: 26px; border-radius: 50%; background: var(--lime); }
  .brand-name { font-size: 24px; font-weight: 700; color: var(--ink); letter-spacing: .5px; }
  .headline { position: absolute; left: 0; right: 0; top: 142px; text-align: center; font-size: 17px; font-weight: 600; color: var(--text-green); }
  .benefits { position: absolute; left: 0; right: 0; top: 180px; list-style: none; text-align: center; font-size: 15px; color: var(--ink); line-height: 20.5px; }
  .benefits li::before { content: "➤"; color: var(--text-green); font-size: 12px; margin-right: 12px; }
  .closing { position: absolute; right: 20px; top: 252px; font-size: 15px; font-weight: 700; font-style: italic; color: var(--text-green); }
  .offer-band { position: absolute; left: 0; bottom: 0; width: 100%; height: 49px; background: var(--forest); color: var(--white); display: flex; align-items: center; justify-content: center; font-family: "Open Sans Condensed", "Open Sans", sans-serif; font-weight: 700; font-size: 18px; letter-spacing: .2px; }
</style>
</head>
<body>

<section class="card card-front" aria-label="Business card front">
  <div class="front-top-band"></div>
  <div class="front-mark"></div>
  <h1 class="holder-name">DANIEL R. HAYES</h1>
  <p class="holder-role">PERSONAL ANANCIAL COACH</p>
  <div class="front-contact-band">
    <ul class="contact-list">
      <li><svg viewBox="0 0 24 24"><path d="M6.6 10.8a15 15 0 0 0 6.6 6.6l2.2-2.2a1 1 0 0 1 1-.25 11.4 11.4 0 0 0 3.6.57 1 1 0 0 1 1 1V20a1 1 0 0 1-1 1A17 17 0 0 1 3 4a1 1 0 0 1 1-1h3.5a1 1 0 0 1 1 1c0 1.25.2 2.45.57 3.57a1 1 0 0 1-.25 1z"/></svg>(555) 014-2298</li>
      <li><svg viewBox="0 0 24 24"><path d="M2 5h20v14H2z M2 5l10 8 10-8" fill="none" stroke="#fff" stroke-width="2.5"/><path d="M2 5h20L12 13z"/></svg>daniel@clearpathmoneyco.com</li>
      <li><svg viewBox="0 0 24 24"><circle cx="12" cy="12" r="10"/><path d="M2 12h20M12 2c3 3 3 17 0 20M12 2c-3 3-3 17 0 20" fill="none" stroke="#3b8a3e" stroke-width="1.6"/></svg>www.clearpathmoneyco.com</li>
    </ul>
  </div>
</section>

<section class="card card-back" aria-label="Business card back">
  <div class="brand">
    <span class="brand-dot"></span>
    <span class="brand-name">CLEARPATH MONEY COACHING</span>
  </div>
  <h2 class="headline">STRUGGLING WITH YOUR FINANCES?</h2>
  <ul class="benefits">
    <li>Learn to become debt free</li>
    <li>Discover the power of cash</li>
    <li>Control your money instead of it controlling you</li>
  </ul>
  <p class="closing">Let us help you achieve a new level of financial freedom!</p>
  <div class="offer-band">SPECIAL OFFER!: FREE 30 MINUTE CONSULTATION</div>
</section>

</body>
</html>
```